Business card - mobile service

O KiraLink is a mobile family safety service based on tablets and smartphones.
The business card must have:
BASIC INFO
Company Logo
Name
Position / Job Title: Co-founder
Mobile Phone Number: +55 (11) 5080 6192
Land Line: +55 (11) 8765 093412
Email Address: name@kiralink-example.com
Web Site URL: www.kiralink-example.com
PROMOTIONAL INFO
Try KiraLink free Today!
Your personal promo code: qqqq-5151-hhhh-3030-9876
Promo code text explanation with the instructions about the trial offer
Updates
Dears,
One more must have: the KiraLink slogan:
Industry/Entity Type
Safety
Look and feel
Each slider illustrates characteristics of the customer's brand and the style your logo design should communicate.

```html
<!DOCTYPE html>
<html lang="en">
<head>
<meta charset="utf-8">
<title>KiraLink business card</title>
<link rel="stylesheet" href="https://fonts.googleapis.com/css2?family=Noto+Sans:ital,wght@0,400;0,700;0,800;1,400&display=swap">
<style>
  :root {
    --stage: #e9ecef;
    --sky: #1ea7e6;
    --sky-light: #5fcaf5;
    --sky-deep: #1290d2;
    --sun: #f2b705;
    --paper: #ffffff;
    --ink: #2b2b2b;
    --muted: #9a9a9a;
  }
  * { box-sizing: border-box; margin: 0; padding: 0; }
  html, body { width: 1200px; height: 944px; overflow: hidden; }
  body {
    background: var(--stage);
    font-family: "Noto Sans", Verdana, sans-serif;
    position: relative;
  }
  .card {
    position: absolute;
    width: 700px;
    height: 400px;
    border-radius: 4px;
    box-shadow: 0 10px 28px rgba(0,0,0,.18);
    overflow: hidden;
  }

  /* Front */
  .card-front {
    left: 130px; top: 60px;
    background: radial-gradient(ellipse at 40% 35%, var(--sky-light) 0%, var(--sky) 50%, var(--sky-deep) 100%);
    color: var(--paper);
    text-align: center;
  }
  .card-front .brand {
    position: absolute; left: 0; right: 0; top: 80px;
    display: flex; justify-content: center; align-items: center; gap: 18px;
  }
  .brand-name {
    font-weight: 800;
    letter-spacing: -1px;
    line-height: 1;
  }
  .card-front .brand-name { font-size: 104px; color: var(--paper); }
  .brand-dot { border-radius: 50%; background: var(--sun); flex: none; }
  .card-front .brand-dot { width: 44px; height: 44px; }
  .front-text {
    position: absolute; left: 40px; right: 40px; top: 236px;
    display: flex; flex-direction: column; align-items: center; gap: 6px;
  }
  .slogan { font-size: 22px; }
  .promo {
    font-size: 22px; color: var(--sun);
    text-transform: uppercase; letter-spacing: 1px;
  }
  .promo-code {
    margin-top: 8px;
    font-size: 18px; font-weight: 700; letter-spacing: 1px;
    padding: 4px 14px;
    border: 1px solid rgba(255,255,255,.7);
    border-radius: 3px;
  }
  .promo-code-label { font-weight: 400; }
  .promo-note { font-size: 14px; opacity: .9; }

  /* Back */
  .card-back {
    left: 370px; top: 484px;
    background: var(--paper);
    color: var(--ink);
  }
  .edge { position: absolute; top: 0; bottom: 0; background: var(--sky); }
  .edge-left { left: 0; width: 10px; }
  .edge-right { right: 0; width: 18px; }
  .card-back .brand {
    position: absolute; left: 0; right: 0; top: 70px;
    display: flex; justify-content: center; align-items: center; gap: 14px;
  }
  .card-back .brand-name { font-size: 76px; color: var(--sky); }
  .card-back .brand-dot { width: 32px; height: 32px; }
  .holder { position: absolute; left: 46px; top: 276px; }
  .holder-name { font-size: 24px; color: var(--sky); }
  .holder-role { font-size: 17px; font-style: italic; }
  .contact {
    position: absolute; left: 378px; top: 262px;
    display: flex; align-items: flex-start; gap: 8px;
    font-size: 16px; line-height: 1.4;
  }
  .contact svg { flex: none; margin-top: 2px; }
  .contact-label { color: var(--sky); }
  .contact-web { color: var(--sky); }
</style>
</head>
<body>
  <section class="card card-front" aria-label="Card front">
    <div class="brand">
      <span class="brand-name">KiraLink</span>
      <span class="brand-dot"></span>
    </div>
    <div class="front-text">
      <p class="slogan">Your Family Safety Service</p>
      <p class="promo">Try KiraLink free Today!</p>
      <p class="promo-code"><span class="promo-code-label">Your code:</span> qqqq-5151-hhhh-3030-9876</p>
      <p class="promo-note">Enter this code in the app to start your 30-day free trial.</p>
    </div>
  </section>

  <section class="card card-back" aria-label="Card back">
    <span class="edge edge-left"></span>
    <span class="edge edge-right"></span>
    <div class="brand">
      <span class="brand-name">KiraLink</span>
      <span class="brand-dot"></span>
    </div>
    <div class="holder">
      <p class="holder-name">Tomas Rivera</p>
      <p class="holder-role">Co-founder</p>
    </div>
    <div class="contact">
      <svg width="16" height="68" viewBox="0 0 16 68" aria-hidden="true">
        <path d="M14 2 C6 2 8 10 8 22 C8 30 6 33 2 34 C6 35 8 38 8 46 C8 58 6 66 14 66" fill="none" stroke="#9a9a9a" stroke-width="2"/>
      </svg>
      <div>
        <p><span class="contact-label">C:</span> +55 (11) 5080 6192</p>
        <p><span class="contact-label">Ph:</span> +55 (11) 8765 093412</p>
        <p><span class="contact-label">E:</span> name@kiralink-example.com</p>
        <p class="contact-web">www.kiralink-example.com</p>
      </div>
    </div>
  </section>
</body>
</html>
```